Business Card Design Project

Business Card
We are rebranding with a new logo
Industry/Entity Type
Business
Contact Information for Business Card
Dennis Morvale +61 487215963 dennis@quorv.com.au P.O. Box 872 Fernlow QLD 4309
Requirements
Must have
- Logo

```html
<!DOCTYPE html>
<html lang="en">
<head>
<meta charset="utf-8">
<title>Quorv International – Business Card</title>
<link rel="stylesheet" href="https://fonts.googleapis.com/css2?family=Ubuntu:wght@400;500&display=swap">
<style>
  :root {
    --bg: #e4e4e4;
    --card: #ffffff;
    --blue: #1a86c4;
    --orange: #e8661c;
    --grey: #8a8a8a;
  }
  * { margin: 0; padding: 0; box-sizing: border-box; }
  html, body {
    width: 1200px;
    height: 898px;
    overflow: hidden;
    background: var(--bg);
    font-family: "Ubuntu", Arial, sans-serif;
  }
  .business-card {
    position: absolute;
    left: 120px;
    top: 156px;
    width: 960px;
    height: 586px;
    background: var(--card);
    box-shadow: 0 6px 18px rgba(0, 0, 0, 0.18);
  }
  .brand {
    position: absolute;
    right: 70px;
    top: 70px;
    text-align: right;
  }
  .brand-name {
    font-size: 40px;
    font-weight: 500;
    color: var(--blue);
    letter-spacing: 1px;
    line-height: 1;
  }
  .contact {
    position: absolute;
    left: 80px;
    bottom: 70px;
  }
  .person-name {
    font-size: 30px;
    font-weight: 500;
    color: var(--blue);
    text-transform: uppercase;
    line-height: 1.05;
    letter-spacing: 1px;
    margin-bottom: 28px;
  }
  .contact-line {
    font-size: 23px;
    color: var(--grey);
    line-height: 1.35;
    letter-spacing: 0.5px;
  }
  .contact-label {
    color: var(--orange);
    font-weight: 500;
  }
  .address {
    position: absolute;
    right: 110px;
    bottom: 190px;
    font-size: 21px;
    color: var(--grey);
    line-height: 1.4;
    letter-spacing: 0.5px;
  }
</style>
</head>
<body>
  <div class="business-card">
    <div class="brand">
      <div class="brand-name">Quorv International</div>
    </div>

    <address class="address" style="font-style: normal;">
      P.O. Box 872<br>
      Fernlow QLD 4309
    </address>

    <div class="contact">
      <div class="person-name">Dennis<br>Morvale</div>
      <div class="contact-line"><span class="contact-label">Cell:</span> +61 487215963</div>
      <div class="contact-line"><span class="contact-label">Email:</span> dennis@quorv.com.au</div>
    </div>
  </div>
</body>
</html>
```